Business Card Design Project

We have recently completed CraftHive projects for a new logo and wesbite.
We now require new business cards.
We hand out very little printed material to clients as all information is online. When we do hand out something, like a business card, we want it to have real impact and make a statement about the quality and professionalism of our company.
We have an idea of what we want our card to look like but we want a designer to make sure they have impact and look great.
Our requirements are…
Size: 85mm X 55mm - Landscape
Front of card: Logo plus the following contact information.
Dennis Marlow
Operations Manager
Phone +44(0) 1632 xxx xxx
Mobile +44(0) 7700 xxx xxx
Email denmo@korvantix.example
Address 17 Pellick Row, Aberdeen AB12 9QZ
Website www.korvantix.example
How you layout the front of the card is up to you, we would like to see some different ideas. Attached are two versions of our logo that may be used.
Back of card: We would like this to be simple but again have impact. Our current thought is to have the logo or just the large W design from the logo in white against a dark background, perhaps made up from the dark green in the logo.
The logos are attached so you can see the colours in them but the dark ones are..
Dark Blue = C:88, M:55, Y:44, K:28
Dark Green = C:87, M:53, Y:50, K:50
We sometimes also use a bright orange as an accent or highlight colour…
Orange: = C:0, M:39, Y:94, K:0

```html
<!DOCTYPE html>
<html lang="en">
<head>
<meta charset="utf-8">
<title>Korvantix Business Cards</title>
<link href="https://fonts.googleapis.com/css2?family=Open+Sans:wght@400;600;700&display=swap" rel="stylesheet">
<style>
  :root {
    --ink-dark: #1f434b;
    --ink-deep: #1c3d44;
    --teal-light: #6fa6ad;
    --olive: #7d945c;
    --paper: #ffffff;
    --backdrop: #ebe8e3;
    --muted: #3c4f54;
  }
  * { margin: 0; padding: 0; box-sizing: border-box; }
  html, body { width: 1200px; height: 800px; overflow: hidden; }
  body {
    position: relative;
    background: var(--backdrop);
    font-family: "Open Sans", Arial, sans-serif;
  }
  .card {
    position: absolute;
    width: 500px;
    height: 323px;
    border-radius: 14px;
    overflow: hidden;
    box-shadow: 0 3px 10px rgba(0,0,0,0.18);
  }
  .card--front { left: 82px; top: 65px; background: var(--paper); }
  .card--dark { left: 611px; top: 67px; background: var(--ink-dark); }
  .card--gradient { left: 86px; top: 408px; background: linear-gradient(90deg, var(--ink-deep) 0%, #4f6b55 50%, var(--olive) 100%); }
  .card--light { left: 611px; top: 408px; background: var(--paper); }

  .front-wave { position: absolute; inset: 0; width: 500px; height: 323px; }

  .brand-block {
    position: absolute;
    left: 42px;
    top: 128px;
    width: 210px;
    display: flex;
    align-items: center;
    gap: 10px;
  }
  .brand-dot { width: 18px; height: 18px; border-radius: 50%; background: var(--ink-dark); flex: none; }
  .brand-name {
    font-weight: 700;
    font-size: 30px;
    letter-spacing: 1px;
    color: var(--ink-dark);
  }

  .contact {
    position: absolute;
    left: 276px;
    top: 80px;
    color: var(--muted);
  }
  .contact__name { font-size: 16px; font-weight: 700; color: var(--ink-dark); letter-spacing: 0.3px; line-height: 20px; }
  .contact__role { font-size: 12.5px; line-height: 18px; margin-bottom: 19px; }
  .contact__list { list-style: none; font-size: 12.5px; line-height: 19px; }
  .contact__list li { display: flex; align-items: center; gap: 5px; }
  .contact__list svg { width: 10px; height: 10px; flex: none; fill: var(--ink-dark); }

  .address {
    position: absolute;
    right: 32px;
    bottom: 17px;
    text-align: right;
    color: var(--paper);
    font-size: 12.5px;
    line-height: 19px;
  }

  .back-mark {
    position: absolute;
    left: 0; right: 0;
    top: 118px;
    display: flex;
    justify-content: center;
    align-items: center;
    gap: 12px;
  }
  .back-mark__dot { width: 22px; height: 22px; border-radius: 50%; flex: none; }
  .back-mark__name { font-weight: 700; font-size: 40px; letter-spacing: 2px; }
  .back-url {
    position: absolute;
    left: 0; right: 0;
    top: 268px;
    text-align: center;
    font-size: 14.5px;
    letter-spacing: 3px;
  }
  .on-dark .back-mark__dot { background: var(--paper); }
  .on-dark .back-mark__name, .on-dark .back-url { color: var(--paper); }
  .on-light .back-mark__dot { background: var(--ink-dark); }
  .on-light .back-mark__name, .on-light .back-url { color: var(--ink-dark); }
</style>
</head>
<body>

  <section class="card card--front" aria-label="Card front">
    <svg class="front-wave" viewBox="0 0 500 323" aria-hidden="true">
      <path d="M0 255 C150 300 360 270 500 178 L500 186 C360 282 150 306 0 262 Z" fill="var(--teal-light)"/>
      <path d="M0 268 C160 310 370 285 500 212 L500 323 L0 323 Z" fill="var(--ink-dark)"/>
      <path d="M330 274 C400 255 455 230 500 196 L500 222 C455 248 400 266 330 274 Z" fill="var(--olive)"/>
    </svg>

    <div class="brand-block">
      <span class="brand-dot"></span>
      <span class="brand-name">KORVANTIX</span>
    </div>

    <div class="contact">
      <p class="contact__name">DENNIS MARLOW</p>
      <p class="contact__role">Operations Manager</p>
      <ul class="contact__list">
        <li><svg viewBox="0 0 10 10"><path d="M2 0.5 L4 2.8 L3 4 C3.6 5.3 4.7 6.4 6 7 L7.2 6 L9.5 8 L8.3 9.5 C4.5 9.3 0.7 5.5 0.5 1.7 Z"/></svg>+44(0) 1632 xxx xxx</li>
        <li><svg viewBox="0 0 10 10"><path d="M2.5 0 H7.5 V10 H2.5 Z M3.3 1 V7.8 H6.7 V1 Z"/></svg>+44(0) 7700 xxx xxx</li>
        <li><svg viewBox="0 0 10 10"><path d="M0 2 H10 V8.5 H0 Z M0.8 2.6 L5 5.6 L9.2 2.6" stroke="var(--paper)" stroke-width="0.8"/></svg>denmo@korvantix.example</li>
        <li><svg viewBox="0 0 10 10"><circle cx="5" cy="5" r="4.5"/><path d="M0.5 5 H9.5 M5 0.5 V9.5 M2.5 2 C4 4 4 6 2.5 8 M7.5 2 C6 4 6 6 7.5 8" stroke="var(--paper)" stroke-width="0.7" fill="none"/></svg>www.korvantix.example</li>
      </ul>
    </div>

    <p class="address">17 Pellick Row<br>Aberdeen AB12 9QZ</p>
  </section>

  <section class="card card--dark on-dark" aria-label="Card back, dark">
    <div class="back-mark"><span class="back-mark__dot"></span><span class="back-mark__name">KORVANTIX</span></div>
    <p class="back-url">www.korvantix.example</p>
  </section>

  <section class="card card--gradient on-dark" aria-label="Card back, gradient">
    <div class="back-mark"><span class="back-mark__dot"></span><span class="back-mark__name">KORVANTIX</span></div>
    <p class="back-url">www.korvantix.example</p>
  </section>

  <section class="card card--light on-light" aria-label="Card back, light">
    <div class="back-mark"><span class="back-mark__dot"></span><span class="back-mark__name">KORVANTIX</span></div>
    <p class="back-url">www.korvantix.example</p>
  </section>

</body>
</html>
```